Real Estate Company / Capital Needs Cards!

need business cards designed using the logos that were just designed by pixelbarn.

Reason: per designers request deadline extended 1 day…thank you.

Target Market(s)

Investors and clients looking to purchase real estate or invest in the business.

Industry/Entity Type

Business

Requirements
Must have
• two designs - one for the real estate logo and one for the capital logo, similar but slightly different.
Nice to have
• something to make it pop (perhaps on the back)
Should not have
• much color

```html
<!DOCTYPE html>
<html lang="en">
<head>
<meta charset="utf-8">
<title>Aldren Real Estate – Business Cards</title>
<link rel="stylesheet" href="https://fonts.googleapis.com/css2?family=Marcellus&family=PT+Sans:wght@400;700&display=swap">
<style>
  :root {
    --bg: #e6e3df;
    --card: #050505;
    --silver-light: #f2f2f0;
    --silver-mid: #d6d5d2;
    --silver-dark: #a9a8a4;
    --ink: #111111;
    --white: #ffffff;
  }
  * { margin: 0; padding: 0; box-sizing: border-box; }
  html, body { width: 1200px; height: 434px; overflow: hidden; background: var(--bg); }
  .canvas { position: relative; width: 1200px; height: 434px; }

  .card {
    position: absolute;
    top: 72px;
    width: 520px;
    height: 290px;
    background: var(--card);
    border-radius: 26px;
    box-shadow: 0 8px 18px rgba(0,0,0,0.25);
    overflow: hidden;
  }
  .card--front { left: 50px; }
  .card--back { left: 630px; }

  .brand { position: absolute; display: flex; align-items: center; }
  .brand__mark { background: linear-gradient(135deg, var(--silver-light), var(--silver-dark)); border-radius: 6px; }
  .brand__text { font-family: "Marcellus", serif; color: var(--silver-mid); line-height: 1; }
  .brand__name { display: block; letter-spacing: 1px; }
  .brand__tagline { display: block; letter-spacing: 3px; }

  .card--front .brand { left: 148px; top: 32px; gap: 12px; }
  .card--front .brand__mark { width: 44px; height: 56px; }
  .card--front .brand__name { font-size: 38px; }
  .card--front .brand__tagline { font-size: 14px; margin-top: 3px; }

  .card--back .brand { left: 80px; top: 92px; gap: 22px; }
  .card--back .brand__mark { width: 96px; height: 112px; border-radius: 10px; }
  .card--back .brand__name { font-size: 66px; }
  .card--back .brand__tagline { font-size: 24px; margin-top: 6px; letter-spacing: 5px; }

  .contact-band {
    position: absolute;
    left: 0; right: 0;
    top: 146px;
    height: 100px;
    background: linear-gradient(180deg, var(--silver-dark) 0%, var(--silver-light) 45%, var(--silver-mid) 100%);
    border-top: 2px solid var(--card);
    border-bottom: 2px solid var(--card);
    box-shadow: 0 -4px 0 -2px var(--silver-mid), 0 4px 0 -2px var(--silver-mid);
    display: flex;
    align-items: center;
    font-family: "PT Sans", sans-serif;
    color: var(--ink);
  }
  .contact-band__address {
    width: 262px;
    text-align: right;
    padding-right: 12px;
    font-size: 15px;
    line-height: 1.3;
    margin-top: 22px;
  }
  .contact-band__divider { width: 1px; height: 70px; background: var(--ink); }
  .contact-band__list { list-style: none; padding-left: 10px; font-size: 15.5px; line-height: 1.4; }
  .contact-band__list li { display: flex; align-items: center; gap: 5px; }
  .contact-band__list li:last-child { font-size: 14px; }
  .contact-band__list svg { width: 13px; height: 13px; fill: var(--ink); flex: none; }

  .holder {
    position: absolute;
    left: 0; right: 0;
    top: 258px;
    text-align: center;
    font-family: "PT Sans", sans-serif;
    font-size: 17px;
    color: var(--white);
  }
  .holder strong { font-weight: 700; }
</style>
</head>
<body>
<main class="canvas">

  <section class="card card--front" aria-label="Business card front">
    <div class="brand">
      <span class="brand__mark" aria-hidden="true"></span>
      <span class="brand__text">
        <span class="brand__name">ALDREN</span>
        <span class="brand__tagline">REAL ESTATE</span>
      </span>
    </div>

    <div class="contact-band">
      <p class="contact-band__address">Street Name, City Name<br>State ZipCode</p>
      <span class="contact-band__divider" aria-hidden="true"></span>
      <ul class="contact-band__list">
        <li>
          <svg viewBox="0 0 16 16" aria-hidden="true"><path d="M3.6 1.5l2.3 2.6-1.3 1.7c.9 2 2.4 3.6 4.5 4.6l1.7-1.3 2.6 2.3-1.2 2.1C7.4 13.3 2.6 8.6 1.5 2.8z"/></svg>
          555-210-4837
        </li>
        <li>
          <svg viewBox="0 0 16 16" aria-hidden="true"><rect x="4" y="1" width="8" height="5"/><rect x="1" y="6" width="14" height="7" rx="1"/><rect x="4" y="11" width="8" height="4"/></svg>
          555-210-4852
        </li>
        <li>
          <svg viewBox="0 0 16 16" aria-hidden="true"><path d="M1 4h14v9H1z M1 4l7 5 7-5" stroke="#d6d5d2" stroke-width="1"/></svg>
          aldrenrealestate@mailbox.com
        </li>
      </ul>
    </div>

    <p class="holder"><strong>Your Name,</strong> Title</p>
  </section>

  <section class="card card--back" aria-label="Business card back">
    <div class="brand">
      <span class="brand__mark" aria-hidden="true"></span>
      <span class="brand__text">
        <span class="brand__name">ALDREN</span>
        <span class="brand__tagline">REAL ESTATE</span>
      </span>
    </div>
  </section>

</main>
</body>
</html>
```